Business card for a new innovative and professional lawn care business

We need a business card design for a new lawn care business in Halifax NS Canada. We offer lawn services in Halifax & Bedford. Our services offered include lawn care, garden services, and property maintenance. We take pride in our work and are experienced at what we do. I would like to see a design that is double sided. On the backside I would like the something simple (maybe my logo preferably on blackround (linked below) with website link, Facebook page or something). The front I want to include contact info:
Morgan Pell
phone 902-555-0148
email - brookvaleyards.ca
facebook - Facebook.com/brookvaleyards
Instagram maybe ? - instagram.com/brookvaleyard
Serving Halifax and Bedford for 5 years?
I don't want it to have too much information as I will be passing them out in aim to visit website, or call !
We do want it to include lawn care, garden services and property maintenance.
Basic, catchy, and modern looking !
Logo attached below !

Target Market(s)

Passing business cards to everyone I meet or interact with.

Industry/Entity Type

Lawn Care

Contact Information for Business Card

Double sided with some basic information, with catchy colours and easy to look at.

Font styles to use
Sans Serif

Requirements
Must have
• Must be double sided and have :
• Name, Phone, Email, FB, Website, and 3 main services offered - lawn care, property maintenance, garden services
Nice to have
• Would be nice to have instagram link if it goes well on there
Should not have
• Don't want too much writing or images that are distracting

```html
<!DOCTYPE html>
<html lang="en">
<head>
<meta charset="utf-8">
<title>Brookvale Yards – Business Card</title>
<link href="https://fonts.googleapis.com/css2?family=Lato:wght@400;700;900&display=swap" rel="stylesheet">
<style>
  :root {
    --backdrop: #1e1e1e;
    --card-white: #f7f7f7;
    --lime: #7cb52f;
    --lime-light: #8cc63f;
    --forest: #0f7a3a;
    --ink: #1f2a14;
    --paper-text: #ffffff;
    --icon-bg: #e9f2dc;
  }
  * { box-sizing: border-box; margin: 0; padding: 0; }
  html, body {
    width: 1200px; height: 873px; overflow: hidden;
    background: var(--backdrop);
    font-family: "Lato", sans-serif;
  }
  .stage { position: relative; width: 1200px; height: 873px; }

  .card {
    position: absolute;
    width: 520px; height: 310px;
    border-radius: 18px;
    background: var(--card-white);
    overflow: hidden;
    box-shadow: 0 16px 40px rgba(0,0,0,.55);
  }
  .card--services { left: 60px; top: 282px; }
  .card--contact  { left: 620px; top: 282px; }
  .card__band { position: absolute; inset: 0; width: 100%; height: 100%; }

  .brand {
    position: absolute;
    display: flex; align-items: center; gap: 10px;
    color: var(--forest);
    font-weight: 900;
    font-size: 30px;
    letter-spacing: .5px;
    text-transform: uppercase;
    white-space: nowrap;
  }
  .brand__dot {
    width: 22px; height: 22px; border-radius: 50%;
    background: var(--lime);
    flex: none;
  }

  /* services side */
  .card--services .brand { left: 40px; top: 58px; }
  .tagline {
    position: absolute; left: 74px; top: 112px;
    color: var(--forest); font-size: 14px; font-weight: 700;
  }
  .services {
    position: absolute; left: 0; right: 0; bottom: 26px;
    list-style: none;
    display: flex; justify-content: space-around;
    color: var(--paper-text); font-size: 15px; font-weight: 700;
  }
  .services li { display: flex; align-items: center; gap: 7px; }
  .services li::before {
    content: ""; width: 7px; height: 7px; border-radius: 50%;
    background: var(--paper-text);
  }

  /* contact side */
  .card--contact .brand { left: 0; right: 0; justify-content: center; top: 40px; }
  .person { position: absolute; left: 30px; top: 170px; color: var(--paper-text); }
  .person__name { font-size: 22px; font-weight: 900; text-transform: uppercase; letter-spacing: .3px; }
  .person__role { color: var(--ink); font-size: 14px; font-weight: 700; margin-top: 2px; }

  .contact-list, .social-list {
    position: absolute; list-style: none;
    color: var(--ink); font-weight: 700; font-size: 15px;
  }
  .contact-list { left: 30px; top: 232px; }
  .contact-list li, .social-list li { display: flex; align-items: center; gap: 10px; margin-bottom: 10px; }
  .social-list { right: 26px; top: 160px; }
  .icon {
    width: 22px; height: 22px; border-radius: 50%;
    background: var(--icon-bg);
    display: inline-flex; align-items: center; justify-content: center; flex: none;
  }
  .website { color: var(--paper-text); font-size: 15px; }
</style>
</head>
<body>
<main class="stage">

  <section class="card card--services" aria-label="Card back: services">
    <svg class="card__band" viewBox="0 0 520 310" preserveAspectRatio="none" aria-hidden="true">
      <path d="M0 262 C180 240 360 190 520 118 L520 310 L0 310 Z" fill="var(--forest)"/>
      <path d="M0 272 C180 250 360 200 520 128 L520 310 L0 310 Z" fill="var(--lime-light)"/>
    </svg>
    <div class="brand"><span class="brand__dot"></span>Brookvale Yards</div>
    <p class="tagline">Serving Halifax &amp; Bedford for 5 years</p>
    <ul class="services">
      <li>Lawn Care</li>
      <li>Property Maintenance</li>
      <li>Garden Services</li>
    </ul>
  </section>

  <section class="card card--contact" aria-label="Card front: contact">
    <svg class="card__band" viewBox="0 0 520 310" preserveAspectRatio="none" aria-hidden="true">
      <path d="M0 150 C170 140 360 110 520 82 L520 310 L0 310 Z" fill="var(--forest)"/>
      <path d="M0 160 C170 150 360 120 520 92 L520 310 L0 310 Z" fill="var(--lime)"/>
    </svg>
    <div class="brand"><span class="brand__dot"></span>Brookvale Yards</div>

    <div class="person">
      <p class="person__name">Morgan Pell</p>
      <p class="person__role">Owner / Founder</p>
    </div>

    <ul class="contact-list">
      <li>
        <span class="icon"><svg width="12" height="12" viewBox="0 0 24 24" aria-hidden="true"><path d="M6.6 10.8a15.1 15.1 0 0 0 6.6 6.6l2.2-2.2a1 1 0 0 1 1-.25 11.4 11.4 0 0 0 3.6.57 1 1 0 0 1 1 1V20a1 1 0 0 1-1 1A17 17 0 0 1 3 4a1 1 0 0 1 1-1h3.5a1 1 0 0 1 1 1c0 1.25.2 2.45.57 3.57a1 1 0 0 1-.25 1z" fill="var(--lime)"/></svg></span>
        902-555-0148
      </li>
      <li>
        <span class="icon"><svg width="12" height="12" viewBox="0 0 24 24" aria-hidden="true"><path d="M2 5h20v14H2z" fill="var(--lime)"/><path d="M2 5l10 8 10-8" fill="none" stroke="var(--icon-bg)" stroke-width="2"/></svg></span>
        me@brookvaleyards.ca
      </li>
    </ul>

    <ul class="social-list">
      <li><span class="icon"></span>/brookvaleyards</li>
      <li><span class="icon"></span>brookvaleyard</li>
      <li class="website">www.brookvaleyards.ca</li>
    </ul>
  </section>

</main>
</body>
</html>
```